Personal training and nutrition business needs business card design

We need a business card that outlays our services and invites potential customers to join our team and take the first step to a healthier and more enjoyable life. We cater for any level of fitness and specialize in weight loss and conditioning, strength training, muscle gain and strength endurance. Whether you are just starting off or need some help getting to the next level of your journey we are here to get the job done.
We specialize in one on one or one on two personal training sessions and each program will be custom made to suit individual fitness goals of our clients

```html
<!DOCTYPE html>
<html lang="en">
<head>
<meta charset="utf-8">
<title>Stride &amp; Tempo – Business Card</title>
<link rel="stylesheet" href="https://fonts.googleapis.com/css2?family=Raleway:wght@400;800&family=Lato:wght@400;700&family=Oswald:wght@500&display=swap">
<style>
  :root {
    --bg: #a9a9a9;
    --purple-light: #ab5fa9;
    --purple-deep: #7a4a9f;
    --purple-text: #8b4ea6;
    --ink: #1a1a1a;
    --white: #ffffff;
    --rule: #9a9a9a;
  }
  * { margin: 0; padding: 0; box-sizing: border-box; }
  html, body { width: 1200px; height: 1200px; overflow: hidden; }
  body { background: var(--bg); position: relative; }

  .card {
    position: absolute;
    top: 303px;
    width: 368px;
    height: 594px;
    text-align: center;
    overflow: hidden;
  }
  .card--front {
    left: 201px;
    background: linear-gradient(150deg, var(--purple-light) 0%, #9a58a6 45%, var(--purple-deep) 100%);
    color: var(--white);
  }
  .card--back { left: 599px; background: var(--white); color: var(--ink); }

  .abs { position: absolute; left: 0; right: 0; }

  .brand-dot { position: absolute; left: 50%; border-radius: 50%; transform: translateX(-50%); }
  .card--front .brand-dot { top: 140px; width: 92px; height: 92px; background: var(--white); }
  .card--back .brand-dot { top: 60px; width: 92px; height: 92px; background: linear-gradient(90deg, var(--purple-deep), var(--purple-light)); }

  .brand-name {
    font-family: "Raleway", sans-serif;
    font-weight: 800;
    text-transform: uppercase;
    font-size: 40px;
    line-height: 44px;
    letter-spacing: 1px;
  }
  .card--front .brand-name { top: 262px; color: var(--white); }
  .card--back .brand-name { top: 186px; color: var(--ink); }

  .tagline {
    font-family: "Oswald", sans-serif;
    font-weight: 500;
    font-size: 10.5px;
    letter-spacing: 1px;
    text-transform: uppercase;
  }
  .card--front .tagline { top: 358px; color: var(--white); }
  .card--back .tagline { top: 278px; color: var(--purple-text); }

  .services {
    top: 460px;
    list-style: none;
    font-family: "Raleway", sans-serif;
    font-size: 17px;
    line-height: 24.6px;
    text-transform: uppercase;
  }

  .person-name {
    top: 334px;
    font-family: "Lato", sans-serif;
    font-weight: 700;
    font-size: 24px;
    color: var(--purple-text);
  }
  .person-role { top: 362px; font-family: "Lato", sans-serif; font-size: 16px; }

  .icon-row { top: 396px; display: flex; justify-content: center; align-items: center; gap: 4px; }
  .icon-row .rule { width: 52px; height: 1px; background: var(--rule); margin: 0 4px; }
  .icon { width: 25px; height: 25px; background: var(--purple-text); border-radius: 3px; display: flex; align-items: center; justify-content: center; }

  .contact, .address {
    font-family: "Lato", sans-serif;
    font-size: 17px;
    line-height: 22px;
  }
  .contact { top: 431px; }
  .divider { top: 507px; left: 88px; right: 80px; height: 1px; background: var(--rule); }
  .address { top: 518px; }
</style>
</head>
<body>
  <section class="card card--front">
    <span class="brand-dot"></span>
    <h1 class="abs brand-name">Stride<br>&amp; Tempo</h1>
    <p class="abs tagline">Personal training. Nutrition. Motivation</p>
    <ul class="abs services">
      <li>Weight loss &amp; conditioning</li>
      <li>Strength training</li>
      <li>Muscle gain</li>
      <li>Strength endurance</li>
    </ul>
  </section>

  <section class="card card--back">
    <span class="brand-dot"></span>
    <h2 class="abs brand-name">Stride<br>&amp; Tempo</h2>
    <p class="abs tagline">Personal training. Nutrition. Motivation</p>
    <p class="abs person-name">DANIEL MARSH</p>
    <p class="abs person-role">Managing Director</p>
    <div class="abs icon-row">
      <span class="rule"></span>
      <span class="icon" aria-label="Phone">
        <svg width="15" height="15" viewBox="0 0 16 16"><path d="M2 6c0-2 3-3 6-3s6 1 6 3v1h-3V6H5v1H2z M4 8h8l1 5H3z" fill="#fff"/></svg>
      </span>
      <span class="icon" aria-label="Email">
        <svg width="16" height="12" viewBox="0 0 16 12"><rect x="0.5" y="0.5" width="15" height="11" fill="none" stroke="#fff"/><path d="M0.5 0.5 8 7l7.5-6.5M0.5 11.5 6 6M15.5 11.5 10 6" fill="none" stroke="#fff"/></svg>
      </span>
      <span class="icon" aria-label="Website">
        <svg width="16" height="16" viewBox="0 0 16 16"><circle cx="8" cy="8" r="7" fill="#fff"/><path d="M4 5c2 0 3 1 2 3s1 3 0 5M10 3c0 2 2 2 3 3" fill="none" stroke="#8b4ea6" stroke-width="1.5"/></svg>
      </span>
      <span class="rule"></span>
    </div>
    <p class="abs contact">044-555 010 203<br>hello@stridetempo.com<br>www.stridetempo.com</p>
    <span class="abs divider"></span>
    <p class="abs address">18 Harbour Lane<br>45452, Country Name</p>
  </section>
</body>
</html>
```